BRISKEL Need a luxury modern business card designed.

Need a luxury modern business card designed. refer to the uploaded files for the company name and logo in the zip file under source files. i will making my descion on monday. so please send in before then so if we need to edit we will have the time. we have a trade show coming up and im on a deadline for printer.

Target Market(s)

high end clients

Contact Information for Business Card

Company nAme and logo. Tobias Fennick Co-Founder / Project Manager Office # 555-318-7094 Cell # 555-642-1586 BRISKEL.CA Tobias@briskel-example.ca

Font styles to use
Other font styles liked:
• Modern

Requirements
Must have
• Company name and logo, contact info, using the black, gold and white color scheme.

```html
<!DOCTYPE html>
<html lang="en">
<head>
<meta charset="utf-8">
<title>BRISKEL – Business Card</title>
<link href="https://fonts.googleapis.com/css2?family=Montserrat:wght@400;500;600&display=swap" rel="stylesheet">
<style>
  :root {
    --gold: #8f8257;
    --charcoal: #2b2c2e;
    --paper: #fbfbf9;
    --ink: #1f2022;
    --backdrop: #e8e5df;
  }
  * { margin: 0; padding: 0; box-sizing: border-box; }
  html, body { width: 1200px; height: 859px; overflow: hidden; }
  body {
    background: var(--backdrop);
    font-family: "Montserrat", Arial, sans-serif;
    position: relative;
  }
  .card {
    position: absolute;
    top: 289px;
    width: 502px;
    height: 285px;
    overflow: hidden;
    box-shadow: 0 10px 22px rgba(0,0,0,0.22);
  }
  .card-front { left: 59px; background: var(--paper); }
  .card-back { left: 639px; background: var(--charcoal); }
  .card-bands { position: absolute; inset: 0; width: 100%; height: 100%; }

  .wordmark {
    position: absolute;
    text-align: center;
    color: var(--ink);
  }
  .wordmark-name {
    display: block;
    font-weight: 400;
    letter-spacing: 0.2em;
    line-height: 1;
  }
  .wordmark-tagline {
    display: flex;
    align-items: center;
    gap: 6px;
    font-weight: 500;
    letter-spacing: 0.28em;
    white-space: nowrap;
  }
  .wordmark-tagline::before,
  .wordmark-tagline::after {
    content: "";
    flex: 1;
    height: 1px;
    background: currentColor;
  }
  .card-front .wordmark { left: 24px; top: 26px; width: 150px; }
  .card-front .wordmark-name { font-size: 21px; margin-bottom: 4px; border-bottom: 1px solid var(--ink); padding-bottom: 3px; }
  .card-front .wordmark-tagline { font-size: 5.5px; margin-top: -7px; background: var(--paper); width: max-content; margin-left: auto; margin-right: auto; padding: 0 2px; }
  .card-front .wordmark-tagline::before,
  .card-front .wordmark-tagline::after { display: none; }

  .person { position: absolute; left: 24px; top: 115px; }
  .person-accent {
    position: absolute; left: -24px; top: 2px;
    width: 4px; height: 29px; background: var(--gold);
  }
  .person-name {
    font-size: 16px; font-weight: 600; color: var(--gold);
    letter-spacing: 0.01em; line-height: 1.2;
  }
  .person-role { font-size: 12.5px; color: var(--ink); margin-top: 2px; }

  .contact-list { position: absolute; left: 24px; top: 200px; list-style: none; }
  .contact-item {
    display: flex; align-items: center; gap: 6px;
    font-size: 12.5px; color: var(--ink); height: 17.5px;
  }
  .contact-icon { width: 11px; height: 11px; flex: none; }
  .contact-item strong { font-weight: 500; color: var(--gold); }

  .card-back .wordmark { left: 0; right: 0; top: 160px; color: var(--paper); }
  .card-back .wordmark-name { font-size: 33px; letter-spacing: 0.24em; padding-left: 0.24em; }
  .card-back .wordmark-tagline {
    font-size: 8.5px; width: 245px; margin: 10px auto 0;
    border-top: 1px solid var(--paper); padding-top: 5px;
  }
</style>
</head>
<body>

<section class="card card-front" aria-label="Business card front">
  <svg class="card-bands" viewBox="0 0 502 285" aria-hidden="true">
    <polygon points="286,285 502,69 502,145 362,285" fill="var(--gold)"/>
    <polygon points="362,285 502,145 502,222 439,285" fill="var(--charcoal)"/>
    <polygon points="439,285 502,222 502,285" fill="var(--gold)"/>
  </svg>

  <div class="wordmark">
    <span class="wordmark-name">BRISKEL</span>
    <span class="wordmark-tagline">Luxury Landscapes</span>
  </div>

  <div class="person">
    <span class="person-accent"></span>
    <p class="person-name">TOBIAS FENNICK</p>
    <p class="person-role">Co-Founder | Project Manager</p>
  </div>

  <ul class="contact-list">
    <li class="contact-item">
      <svg class="contact-icon" viewBox="0 0 12 12" aria-hidden="true"><circle cx="6" cy="6" r="5.2" fill="none" stroke="var(--ink)" stroke-width="0.9"/><path d="M4 3.4c-.6.4-.6 1.4.2 2.6s1.9 2 2.6 1.9c.5-.1.8-.5.8-.8l-1-.6-.5.4c-.5-.2-1.1-.8-1.3-1.3l.4-.5-.6-1z" fill="var(--ink)"/></svg>
      <span>555-318-7094</span>
    </li>
    <li class="contact-item">
      <svg class="contact-icon" viewBox="0 0 12 12" aria-hidden="true"><rect x="3.3" y="1" width="5.4" height="10" rx="0.9" fill="none" stroke="var(--ink)" stroke-width="0.9"/><line x1="5.2" y1="9.4" x2="6.8" y2="9.4" stroke="var(--ink)" stroke-width="0.8"/></svg>
      <span>555-642-1586</span>
    </li>
    <li class="contact-item">
      <svg class="contact-icon" viewBox="0 0 12 12" aria-hidden="true"><rect x="1" y="2.6" width="10" height="6.8" fill="none" stroke="var(--ink)" stroke-width="0.9"/><polyline points="1,2.8 6,6.6 11,2.8" fill="none" stroke="var(--ink)" stroke-width="0.9"/></svg>
      <span>Tobias@briskel-example.ca</span>
    </li>
    <li class="contact-item">
      <svg class="contact-icon" viewBox="0 0 12 12" aria-hidden="true"><circle cx="6" cy="6" r="5" fill="none" stroke="var(--ink)" stroke-width="0.9"/><ellipse cx="6" cy="6" rx="2.2" ry="5" fill="none" stroke="var(--ink)" stroke-width="0.8"/><line x1="1" y1="6" x2="11" y2="6" stroke="var(--ink)" stroke-width="0.8"/></svg>
      <span>www.<strong>briskel</strong>.ca</span>
    </li>
  </ul>
</section>

<section class="card card-back" aria-label="Business card back">
  <svg class="card-bands" viewBox="0 0 502 285" aria-hidden="true">
    <polygon points="66,0 143,0 0,141 0,65" fill="var(--gold)"/>
  </svg>

  <div class="wordmark">
    <span class="wordmark-name">BRISKEL</span>
    <span class="wordmark-tagline">Luxury Landscapes</span>
  </div>
</section>

</body>
</html>
```